Business card design for new eCommerce site focusing on integrity and strong businsess tactics

We need a business card that will stand out and be memorable. Something with color that matches our company logo colors. Think high end version of Pactivo. There are 2 logos provided. The parent company is called Amber Ledge Partners and we are presenting a new and very exciting eCommerce site called BrightHarborTrade.example.

Target Market(s)

Our target markets are in the Activities, Food and Beverage, Health and Beauty

Industry/Entity Type

Marketing

Contact Information for Business Card

We have 4 members that need cards...I will provide all info to the winner of the design contest
Business Address is
4870 West 63rd Avenue, Suite C207
Phoenix AZ 85731

Font styles to use
Serif
Sans Serif

Colors

Designer to choose colors to be used in the design.

Requirements
Must have
• The card must be memorable...should be unique in design but must exude integrity and be playful .
• I have provided several colors or our parent company...please feel free to use which ever
Nice to have
• I will leave this up to you. Feel free to use other images of your choosing that wraps around our client.....Activities, Dining, Health, Beauty
Should not have
• just dont be boring

```html
<!DOCTYPE html>
<html lang="en">
<head>
<meta charset="utf-8">
<title>Amber Ledge Partners &amp; BrightHarborTrade business cards</title>
<link rel="stylesheet" href="https://fonts.googleapis.com/css2?family=Montserrat:wght@400;700&family=Varela+Round&display=swap">
<style>
  :root {
    --backdrop: #1e1e1e;
    --brand-blue: #2a7db5;
    --brand-blue-deep: #1d6ea6;
    --brand-blue-light: #3389c2;
    --brand-green: #7cc242;
    --card-white: #ffffff;
    --ink-grey: #555a5e;
    --divider: #9a9a9a;
  }
  * { box-sizing: border-box; margin: 0; padding: 0; }
  html, body { width: 1200px; height: 897px; overflow: hidden; background: var(--backdrop); }
  .canvas { position: relative; width: 1200px; height: 897px; }

  .card { position: absolute; overflow: hidden; }

  /* Front: parent company */
  .card-front {
    left: 354px; top: 162px; width: 486px; height: 276px;
    background: linear-gradient(160deg, var(--brand-blue-deep), var(--brand-blue-light));
    font-family: "Montserrat", sans-serif; color: var(--card-white); text-align: center;
  }
  .front-mark {
    position: absolute; left: 50%; top: 58px; width: 40px; height: 40px;
    margin-left: -20px; border-radius: 50%; border: 3px solid var(--card-white);
  }
  .front-name {
    position: absolute; left: 0; right: 0; top: 120px;
    font-size: 29px; font-weight: 700; letter-spacing: 0.2px;
  }
  .front-web {
    position: absolute; left: 0; right: 0; top: 244px;
    font-size: 11px; letter-spacing: 1.3px;
  }

  /* Back: eCommerce site */
  .card-back {
    left: 348px; top: 468px; width: 492px; height: 278px;
    background: var(--card-white); font-family: "Varela Round", sans-serif;
  }
  .side-strip { position: absolute; left: 0; top: 0; width: 24px; height: 100%; background: var(--brand-blue); }
  .side-strip .accent { position: absolute; left: 0; top: 130px; width: 24px; height: 43px; background: var(--brand-green); border-top: 2px solid #fff; border-bottom: 2px solid #fff; }
  .side-icons { position: absolute; left: 7px; top: 202px; width: 10px; }
  .side-icons svg { display: block; margin-bottom: 4px; }

  .site-logo { position: absolute; left: 43px; top: 42px; display: flex; align-items: center; gap: 8px; }
  .site-logo .dot { width: 16px; height: 16px; border-radius: 50%; background: var(--brand-blue); }
  .site-logo .name { font-size: 18px; color: var(--brand-green); white-space: nowrap; }
  .site-tagline { position: absolute; left: 67px; top: 66px; font-size: 8.5px; letter-spacing: 0.8px; color: var(--ink-grey); }

  .person-name { position: absolute; left: 43px; top: 134px; font-size: 17px; letter-spacing: 0.6px; color: var(--brand-blue); }
  .person-role { position: absolute; left: 43px; top: 156px; font-size: 13px; color: var(--ink-grey); }

  .contact {
    position: absolute; top: 200px; font-size: 9.5px; line-height: 15px;
    color: var(--ink-grey); white-space: nowrap;
  }
  .contact-lines { left: 43px; }
  .contact-address { left: 230px; }
  .contact-divider { position: absolute; left: 218px; top: 203px; width: 1px; height: 39px; background: var(--divider); }

  .corner-sweep { position: absolute; left: 0; top: 0; }
</style>
</head>
<body>
<main class="canvas">

  <section class="card card-front" aria-label="Amber Ledge Partners card front">
    <div class="front-mark"></div>
    <h1 class="front-name">Amber Ledge Partners</h1>
    <p class="front-web">www.amberledgepartners.example</p>
  </section>

  <section class="card card-back" aria-label="BrightHarborTrade card back">
    <svg class="corner-sweep" width="492" height="278" viewBox="0 0 492 278" aria-hidden="true">
      <path d="M190 278 Q370 262 492 186 L492 278 Z" fill="var(--brand-blue)"/>
      <path d="M180 278 Q362 258 492 178" fill="none" stroke="var(--brand-green)" stroke-width="3"/>
    </svg>

    <div class="side-strip">
      <div class="accent"></div>
      <div class="side-icons" aria-hidden="true">
        <svg width="10" height="11" viewBox="0 0 10 11"><rect x="2.5" y="0.5" width="5" height="9" rx="1" fill="none" stroke="#fff" stroke-width="1.2"/></svg>
        <svg width="10" height="11" viewBox="0 0 10 11"><rect x="1" y="2" width="8" height="6" fill="#fff"/><path d="M1 2 L5 5.5 L9 2" fill="none" stroke="var(--brand-blue)" stroke-width="1"/></svg>
        <svg width="10" height="11" viewBox="0 0 10 11"><circle cx="4.3" cy="4.3" r="3" fill="none" stroke="#fff" stroke-width="1.5"/><path d="M6.5 6.5 L9 9" stroke="#fff" stroke-width="1.8"/></svg>
      </div>
    </div>

    <div class="site-logo">
      <span class="dot"></span>
      <span class="name">BrightHarborTrade.example</span>
    </div>
    <p class="site-tagline">Activities-Dining-Health-Beauty</p>

    <h2 class="person-name">Daniel Reyes</h2>
    <p class="person-role">Founder</p>

    <p class="contact contact-lines">0420 555 318<br>info@brightharbortrade.example<br>www.brightharbortrade.example</p>
    <span class="contact-divider"></span>
    <p class="contact contact-address">4870 West 63rd<br>Avenue, Suite C207<br>Phoenix AZ 85731</p>
  </section>

</main>
</body>
</html>
```